Design website home page for pathology consulting company

Starting a new consulting company with anatomic pathologists focused on expert diagnosis and second opinions on difficult pathology cases. In the near future we will be incorporating next generation diagnostics for rare diseases of childhood into the business. These include discovery and testing of DNA for mutations.

The company is formed around one of the best known pathologists in the world named Marcel "Biscuit" Trowell. The name of the company is "BiscuitLab"

We had a logo design by SketchForum - it is great. I will attach file as soon as I have it (contest ending today). Our company is medical, uses microscopes, DNA, probably will focus on childhood diseases but not solely on childhood diseases. we're not particularly conservative, but the customers we want to appeal to include older practicing pathologists as well as patients (sometimes parents) looking for second opinions.

Think a group of expert doctors diagnosing disease through the microscope and through DNA technology, ages ranging from 35-75 all trained by the best pathologist in the world - "Biscuit"

We receive glass slides from diseases from patients all over the world from docs who need an expert to tell them what is the diagnosis. So "path to the diagnosis" is also part of the company marketing message.

We want the website design to describe our company but be very simple to find what one is looking for as we will use it as the launch page to:
1) order services
2) check results/reports
3) set up new account
4) speak with one of the pathologists
5) see our test menu
6) access our educational material/webinars
Updates

Update - looking for home page design and then finalists will ask for second page design to keep with theme - ok?

Reason: realized this project isn't web design but web home page design - thanks

Reason: Holidays for some in next two weeks

Reason: Hot discussion among collaborators for a few of the submissions. Will provide detail individually this weekend. Thanks so much for all the submissions!

Target Market(s)

Referring pathologists, physicians who want second opinions on pathology disease diagnosis, patients who have had biopsies (either patients themselves or parents of patients), generally high education level

Industry/Entity Type

Marketing

Requirements
Must have
• BiscuitLab
Next Generation Pathology Consultants

```html
<!DOCTYPE html>
<html lang="en">
<head>
<meta charset="utf-8">
<title>BiscuitLab — Next Generation Pathology Consultants</title>
<link href="https://fonts.googleapis.com/css2?family=Open+Sans:wght@400;600&family=PT+Sans:wght@400;700&display=swap" rel="stylesheet">
<style>
:root{
  --brand:#1d5496;
  --ink:#222;
  --heading:#555;
  --text:#777;
  --muted:#8a8a8a;
  --nav-bg:#f5f5f5;
  --nav-active:#e7e7e7;
  --section-bg:#f4f4f4;
  --line:#dcdcdc;
  --white:#fff;
}
*{margin:0;padding:0;box-sizing:border-box}
html,body{width:1200px;height:1200px;overflow:hidden;background:var(--white)}
body{position:relative;font-family:"PT Sans",Arial,sans-serif;color:var(--ink)}
.abs{position:absolute}

/* header */
.brand-mark{left:236px;top:34px;width:60px;height:60px;border-radius:50%;background:var(--brand)}
.brand-name{left:185px;top:102px;font-family:"Open Sans",sans-serif;font-weight:400;font-size:27px;color:var(--brand);letter-spacing:.8px;line-height:1.1}
.brand-tagline{left:187px;top:133px;font-size:9px;color:var(--muted);font-family:"Open Sans",sans-serif;white-space:nowrap}
.welcome{left:734px;top:60px;font-size:12px;color:var(--ink);letter-spacing:.3px}
.account-links{left:909px;top:59px;font-size:13px;color:var(--muted);display:flex;gap:20px}
.connect{left:856px;top:112px;font-size:9px;color:var(--muted);letter-spacing:.3px}
.social{top:107px;width:21px;height:21px}

/* nav */
.main-nav{left:0;top:172px;width:1200px;height:65px;background:var(--nav-bg)}
.main-nav a{position:absolute;top:0;height:65px;line-height:70px;font-size:15px;color:#666;text-decoration:none;text-transform:uppercase}
.main-nav a.active{background:var(--nav-active);padding:0 24px;left:202px}

/* hero */
.hero{left:0;top:237px;width:1200px;height:426px;
  background:linear-gradient(90deg,#c9d4d3 0%,#f1f1f1 25%,#ecebea 50%,#dfe5e5 72%,#c7d3d2 100%)}
.hero-title{left:700px;top:383px;font-family:"Open Sans",sans-serif;font-weight:400;font-size:31px;line-height:42px;color:var(--brand);letter-spacing:.2px}
.hero-text{left:700px;top:491px;font-family:"Open Sans",sans-serif;font-size:11.6px;line-height:15px;color:var(--brand)}
.hero-link{left:700px;top:564px;font-size:16px;color:var(--brand);display:flex;align-items:center;gap:14px}

/* features */
.feature{top:724px;width:300px;text-align:center}
.feature-icon{width:88px;height:88px;margin:0 auto}
.feature-title{margin-top:25px;font-family:"Open Sans",sans-serif;font-weight:400;font-size:24px;color:var(--heading)}
.feature-text{margin-top:14px;font-family:"Open Sans",sans-serif;font-size:14px;line-height:21px;color:var(--text)}

/* order */
.order{left:0;top:993px;width:1200px;height:207px;background:var(--section-bg);border-top:1px solid #eaeaea}
.order-title{left:183px;top:1056px;font-family:"Open Sans",sans-serif;font-weight:400;font-size:28px;color:#333}
.order-item{left:180px;display:flex;align-items:center;gap:20px;font-size:16.5px;color:#555}
.order-rule{left:180px;top:1158px;width:290px;height:2px;background:var(--line)}
.order-card{left:677px;top:1056px;width:353px;height:144px;background:var(--white)}
.order-card-title{left:780px;top:1101px;font-family:"Open Sans",sans-serif;font-weight:400;font-size:28px;color:#333}
.field{left:722px;top:1175px;width:264px;height:30px;border:1px solid var(--line);background:#f7f7f7;font-family:"Open Sans",sans-serif;font-size:11px;color:#555;padding:8px 0 0 23px}
</style>
</head>
<body>

<header>
  <div class="abs brand-mark"></div>
  <div class="abs brand-name">BiscuitLab</div>
  <div class="abs brand-tagline">Next Generation Pathology Consultants</div>
  <div class="abs welcome">WELCOME MESSAGE!</div>
  <div class="abs account-links"><span>Sign Up</span><span>|</span><span>Login</span></div>
  <div class="abs connect">connect with us</div>
  <svg class="abs social" style="left:946px" viewBox="0 0 21 21"><circle cx="10.5" cy="10.5" r="10.5" fill="var(--brand)"/><path d="M7 5.5l2 2-1.2 1.5a7 7 0 0 0 3.2 3.2l1.5-1.2 2 2-1.3 1.6C10 14.5 6.5 11 5.4 7z" fill="#fff"/></svg>
  <svg class="abs social" style="left:976px" viewBox="0 0 21 21"><circle cx="10.5" cy="10.5" r="10.5" fill="var(--brand)"/><rect x="5.5" y="7" width="10" height="7" rx="1" fill="#fff"/><path d="M5.8 7.4l4.7 3.6 4.7-3.6" stroke="var(--brand)" fill="none" stroke-width="1"/></svg>
  <svg class="abs social" style="left:1007px" viewBox="0 0 21 21"><circle cx="10.5" cy="10.5" r="10.5" fill="var(--brand)"/><circle cx="9.6" cy="9.6" r="3" stroke="#fff" stroke-width="1.3" fill="none"/><path d="M11.8 11.8l3 3" stroke="#fff" stroke-width="1.5"/></svg>
</header>

<nav class="abs main-nav">
  <a class="active" href="#">Home</a>
  <a style="left:311px" href="#">Services</a>
  <a style="left:416px" href="#">Medical Reports</a>
  <a style="left:582px" href="#">Our Doctors</a>
  <a style="left:724px" href="#">Patients</a>
  <a style="left:829px" href="#">FAQ' s</a>
  <a style="left:913px" href="#">Contact</a>
</nav>

<div class="abs hero" role="img" aria-label="Photo of pathologists in lab coats and safety glasses working at a microscope"></div>
<h1 class="abs hero-title">VERITATIS EXPLICABO<br>DOLORES UT&nbsp; DICTA</h1>
<p class="abs hero-text">Lorem ipsum dolor amet rem eos illo omnis<br>aut aperiam ab ipsam ipsa odit aut aperiam<br>aut aspernatur veritatis unde unde sed enim</p>
<div class="abs hero-link">Learn More
  <svg width="22" height="22" viewBox="0 0 22 22"><circle cx="11" cy="11" r="10" stroke="var(--brand)" stroke-width="1.5" fill="none"/><path d="M9 6.5l4.5 4.5L9 15.5" stroke="var(--brand)" stroke-width="1.6" fill="none"/></svg>
</div>

<section>
  <div class="abs feature" style="left:167px">
    <svg class="feature-icon" viewBox="0 0 88 88"><circle cx="44" cy="44" r="44" fill="var(--brand)"/><path d="M28 26h22l10 10v26H28z M50 26v10h10" stroke="#fff" stroke-width="2" fill="none" stroke-linejoin="round"/></svg>
    <h2 class="feature-title">Medical Reports</h2>
    <p class="feature-text">Dolores voluptatem dolorem beatiae<br>atione ratione dolores&nbsp; veritatis unde</p>
  </div>
  <div class="abs feature" style="left:450px">
    <svg class="feature-icon" viewBox="0 0 88 88"><circle cx="44" cy="44" r="44" fill="var(--brand)"/><path d="M28 26h22l10 10v26H28z M50 26v10h10" stroke="#fff" stroke-width="2" fill="none" stroke-linejoin="round"/><path d="M36 42h16M36 47h16M36 52h16M36 57h16" stroke="#fff" stroke-width="2"/></svg>
    <h2 class="feature-title">Test Menu</h2>
    <p class="feature-text">Dolores voluptatem dolorem beatiae<br>atione ratione dolores&nbsp; veritatis unde</p>
  </div>
  <div class="abs feature" style="left:735px">
    <svg class="feature-icon" viewBox="0 0 88 88"><circle cx="44" cy="44" r="44" fill="var(--brand)"/><path d="M28 26h22l10 10v26H28z M50 26v10h10" stroke="#fff" stroke-width="2" fill="none" stroke-linejoin="round"/><path d="M40 42l-4 5 4 5M48 42l4 5-4 5" stroke="#fff" stroke-width="2" fill="none"/></svg>
    <h2 class="feature-title">Webinars</h2>
    <p class="feature-text">Dolores voluptatem dolorem beatiae<br>atione ratione dolores&nbsp; veritatis unde</p>
  </div>
</section>

<section class="abs order"></section>
<h2 class="abs order-title">Order Service</h2>
<div class="abs order-item" style="top:1122px">
  <svg width="22" height="22" viewBox="0 0 22 22"><circle cx="11" cy="11" r="10" stroke="var(--brand)" stroke-width="1.5" fill="none"/><path d="M6.5 11h9" stroke="var(--brand)" stroke-width="1.6"/></svg>Fugit aut illo omnis explicabo ipsa</div>
<div class="abs order-rule"></div>
<div class="abs order-item" style="top:1171px">
  <svg width="22" height="22" viewBox="0 0 22 22"><circle cx="11" cy="11" r="10" stroke="var(--brand)" stroke-width="1.5" fill="none"/><path d="M6.5 11h9" stroke="var(--brand)" stroke-width="1.6"/></svg>Rem ipsam quai illo dolores</div>

<div class="abs order-card"></div>
<svg class="abs" style="left:721px;top:1094px" width="38" height="48" viewBox="0 0 38 48"><path d="M8 1h18l10 10v30H8z M26 1v10h10" stroke="var(--brand)" stroke-width="1.6" fill="#fff" stroke-linejoin="round"/><path d="M2 7v40h26" stroke="var(--brand)" stroke-width="1.6" fill="none"/></svg>
<h2 class="abs order-card-title">Order Form</h2>
<div class="abs field">full name</div>

</body>
</html>
```